Postcard design to acquire new clients for my Property Management Company

I'm looking for a postcard design that I can send to prospective clients detailing information about my company and services.
Postcard should be eye catching and contain information from www.bramblecrestpm.com. I've provided a few screen shots for the most important information and my logo.
Target Market(s)
Real Estate
Industry/Entity Type
Real Estate
Font styles to use
Sans Serif
Requirements
Must have
- Must be eye catching!! this will be a direct mail piece - I'd like for the card to be read and not tossed in the trash immediately.
Design que from the logo.
A place to write / print the receipts name and address.
our physical address - 2387 Hollow Pine Road, Lubbock, TX 79852.
Should not have
- the contact information on the business card is not accurate - please use info from website.

```html
<!DOCTYPE html>
<html lang="en">
<head>
<meta charset="utf-8">
<title>Bramblecrest Property Management – Postcard</title>
<link rel="stylesheet" href="https://fonts.googleapis.com/css2?family=Montserrat:wght@400;500;600;700;800&family=Arimo:wght@400&display=swap">
<style>
  :root {
    --navy: #1d5189;
    --navy-deep: #163f6e;
    --band: rgba(27, 82, 141, 0.93);
    --grey-band: #a4a5a7;
    --panel-light: #ececec;
    --ink: #111;
    --muted: #555;
    --rule: #9a9a9a;
    --white: #ffffff;
    --backdrop: #e7e5e2;
  }
  * { box-sizing: border-box; margin: 0; padding: 0; }
  html, body { width: 1071px; height: 1200px; overflow: hidden; background: var(--backdrop); }
  body { position: relative; font-family: "Montserrat", sans-serif; }

  .card {
    position: absolute; left: 115px; width: 840px; height: 560px;
    overflow: hidden; background: var(--white);
    box-shadow: 0 2px 8px rgba(0,0,0,0.18);
  }
  .card--front { top: 27px; }
  .card--back { top: 613px; }

  /* Front */
  .front-photo {
    position: absolute; inset: 0;
    background: linear-gradient(100deg, #3b4657 0%, #6f7480 30%, #9da2a9 55%, #d7dbde 78%, #eef0f1 100%);
  }
  .logo-panel { position: absolute; top: 0; left: 0; width: 840px; height: 97px; }
  .brand-front {
    position: absolute; top: 18px; right: 29px; text-align: right;
    color: var(--navy); line-height: 1;
  }
  .brand-front .brand-name { font-size: 30px; font-weight: 700; letter-spacing: 4px; }
  .brand-front .brand-sub { font-size: 15px; font-weight: 500; letter-spacing: 3.6px; margin-top: 8px; }

  .headline-band {
    position: absolute; left: 0; top: 413px; width: 840px; height: 115px;
    background: var(--band); color: var(--white);
  }
  .headline {
    position: absolute; left: 38px; right: 36px; top: 20px;
    font-size: 30px; font-weight: 700; text-align: center; letter-spacing: -0.3px;
  }
  .headline-rule { position: absolute; left: 40px; right: 36px; top: 61px; height: 2px; background: var(--white); }
  .tagline {
    position: absolute; left: 38px; right: 36px; top: 70px;
    font-family: "Arimo", sans-serif; font-size: 22px; text-align: center;
  }

  /* Back */
  .services-panel { position: absolute; left: 0; top: 0; width: 416px; height: 461px; }
  .services-photo {
    position: absolute; inset: 0;
    background: linear-gradient(135deg, #1c4f87 0%, #2a5e97 45%, #3a6ca3 70%, #23578f 100%);
  }
  .services-title {
    position: absolute; left: 40px; top: 40px; color: var(--white);
    font-size: 31px; font-weight: 700; line-height: 0.95;
  }
  .services-intro {
    position: absolute; left: 43px; top: 101px; color: var(--white);
    font-size: 15px; font-weight: 400; line-height: 1.15;
  }
  .service-list { list-style: none; position: absolute; left: 43px; top: 160px; }
  .service-list li {
    display: flex; align-items: center; height: 33.7px;
    color: var(--white); font-size: 17.5px; font-weight: 600;
  }
  .service-list svg { width: 26px; height: 22px; margin-right: 16px; fill: var(--white); }

  .contact-band {
    position: absolute; left: 0; top: 461px; width: 416px; height: 99px;
    background: var(--grey-band); color: var(--white); text-align: center;
  }
  .contact-phone { position: absolute; left: 0; right: 0; top: 8px; font-size: 45px; font-weight: 700; letter-spacing: -0.5px; }
  .contact-web { position: absolute; left: 0; right: 0; top: 63px; font-size: 21px; font-weight: 700; }

  .address-side { position: absolute; left: 416px; top: 0; width: 424px; height: 560px; background: var(--white); }
  .brand-back { position: absolute; left: 42px; top: 77px; color: var(--navy); line-height: 1; }
  .brand-back .brand-name { font-size: 19px; font-weight: 700; letter-spacing: 2.6px; }
  .brand-back .brand-sub { font-size: 9.5px; font-weight: 500; letter-spacing: 2.2px; margin-top: 5px; }
  .return-address {
    position: absolute; left: 42px; top: 116px;
    font-size: 10px; font-weight: 500; line-height: 1.35; color: var(--muted); font-style: normal;
  }
  .stamp-box { position: absolute; left: 270px; top: 48px; width: 98px; height: 98px; border: 1px solid #555; }
  .to-label { position: absolute; left: 62px; top: 206px; font-size: 15px; font-weight: 700; color: var(--ink); }
  .address-line { position: absolute; left: 62px; width: 308px; height: 1px; background: var(--rule); }
</style>
</head>
<body>

<section class="card card--front">
  <div class="front-photo" role="img" aria-label="Photo of a property manager showing a young couple the window of a bright rental home"></div>
  <svg class="logo-panel" viewBox="0 0 840 97" aria-hidden="true">
    <polygon points="421,0 840,0 840,97 488,97" fill="#ececec"/>
  </svg>
  <div class="brand-front">
    <div class="brand-name">BRAMBLECREST</div>
    <div class="brand-sub">PROPERTY MANAGEMENT</div>
  </div>
  <div class="headline-band">
    <h1 class="headline">PROPERTY MANAGEMENT ACROSS LUBBOCK, TX</h1>
    <div class="headline-rule"></div>
    <p class="tagline">Maximize your financial returns with support from our rental specialists</p>
  </div>
</section>

<section class="card card--back">
  <div class="services-panel">
    <div class="services-photo" role="img" aria-label="Blue-toned photo of house keys being handed over"></div>
    <h2 class="services-title">DISCOVER<br>OUR SERVICES</h2>
    <p class="services-intro">We offer full-service property<br>management solutions</p>
    <ul class="service-list">
      <li><svg viewBox="0 0 26 22"><path d="M13 1 1 11h3v10h7v-6h4v6h7V11h3z"/></svg>Property Marketing</li>
      <li><svg viewBox="0 0 26 22"><circle cx="8" cy="6" r="4"/><circle cx="18" cy="6" r="4"/><path d="M0 20c0-5 4-8 8-8s8 3 8 8zM14 20c0-3-1-5-2-7 2-1 4-1 6-1 4 0 8 3 8 8z"/></svg>Tenant Screening</li>
      <li><svg viewBox="0 0 26 22"><text x="13" y="19" font-size="22" font-weight="700" text-anchor="middle" font-family="Montserrat, sans-serif" fill="#fff">$</text></svg>Rent Collection</li>
      <li><svg viewBox="0 0 26 22"><path d="M9 3h10l3 3-4 1-11 13-3-2L15 6l-6-1z"/></svg>Maintenance</li>
      <li><svg viewBox="0 0 26 22"><circle cx="11" cy="9" r="6.5" fill="none" stroke="#fff" stroke-width="3"/><path d="M15 13l3-2 6 8-3 2z"/></svg>Property Inspections</li>
      <li><svg viewBox="0 0 26 22"><path d="M2 2h2v16h21v2H2z"/><rect x="7" y="10" width="2.5" height="6"/><rect x="11" y="6" width="2.5" height="10"/><rect x="15" y="8" width="2.5" height="8"/><rect x="19" y="4" width="2.5" height="12"/></svg>Financial Reporting</li>
      <li><svg viewBox="0 0 26 22"><path d="M13 1 4 4v6c0 6 4 10 9 11 5-1 9-5 9-11V4z"/></svg>Evictions</li>
      <li><svg viewBox="0 0 26 22"><path d="M12 2h2v16h5v2H7v-2h5zM3 6h20v1.5H3zM5 7 1 15h8zM21 7l-4 8h8z"/></svg>Legal Guidance</li>
    </ul>
  </div>
  <div class="contact-band">
    <div class="contact-phone">(806)555-0147</div>
    <div class="contact-web">WWW.BRAMBLECRESTPM.COM</div>
  </div>
  <div class="address-side">
    <div class="brand-back">
      <div class="brand-name">BRAMBLECREST</div>
      <div class="brand-sub">PROPERTY MANAGEMENT</div>
    </div>
    <address class="return-address">2387 Hollow Pine Road<br>Lubbock, TX 79852</address>
    <div class="stamp-box"></div>
    <div class="to-label">TO</div>
    <div class="address-line" style="top:265px"></div>
    <div class="address-line" style="top:314px"></div>
    <div class="address-line" style="top:359px"></div>
    <div class="address-line" style="top:409px"></div>
  </div>
</section>

</body>
</html>
```